Professional Engineering Web Design

Project Brief: Website Redesign for Mechanical Design Consultancy
Project Overview
I want to update and improve my current website to create a more professional, modern, and high-credibility online presence for my mechanical design consultancy.

Current site: https://valtorix.design/

The new website must communicate expertise, precision, and trust—matching the standard of top engineering and product design agencies.

Reference Websites (Style + Structure Inspiration)
These represent the quality, cleanliness, and professionalism I want to achieve:

https://plinthwaredesign.com/
https://www.sorvane.com/
https://bramlow-uk.com/
Brand Look
Professional, modern, engineering-focused aesthetic
Clean layouts and strong typography
High-quality imagery conveying precision, innovation, and mechanical expertise
Colour scheme and styling must follow my existing logo (attached in project)
Platform Requirements
The website must be built on WordPress
Should use a clean, flexible theme or modern page builder (Elementor, Gutenberg, Bricks, or similar)
Avoid overly complex custom coding so I can easily edit content later
Final deliverable must allow me to manage and update content without developer assistance
Functionality
Fast-loading, lightweight, and smooth user experience
Clean animations and transitions similar to the reference sites
Fully mobile responsive
Clear navigation and strong visual hierarchy
Contact forms optimised for lead generation
Optional: subtle scroll effects, case study sliders, icon animations, etc.
SEO Aspirations
Developer should recommend and implement a modern SEO strategy
Proper on-page SEO setup (titles, meta, schema, alt tags, heading structure)
Optimised site architecture for ranking and crawling
Aim: Generate leads through improved visibility and keyword targeting
Optional but useful: plain review badge Analytics, plain review badge Search Console setup
User Journeys
(Recommended structure)

The site should be crafted around clear, intuitive journeys for each type of visitor:

Potential new clients
Quickly understand what services I offer
View examples of past work / case studies
See credibility indicators (process, expertise, industries served)
Easily contact me or request a project discussion
Returning clients
Access updated portfolio items
Find contact details or book follow-up work easily
General visitors discovering through SEO
Be guided to core service areas
Understand my value proposition quickly
Be invited to learn more or make contact
The developer should design the structure to support these journeys smoothly.

Maintenance Expectations
Website will be maintained by me, so it should be easy to update using relatively basic WordPress skills
Use modular templates and simple backend structure
Avoid unnecessary plugins
Provide brief handover documentation if required
Hosting Preferences
Site is currently hosted via a family member
Open to discussing moving to a paid, reliable hosting provider if preferable for performance and maintainability
Developer may advise on the best hosting setup for WordPress
Content
Most content can be taken from the existing website
Developer is welcome to suggest improvements to structure, layout, and imagery
Must remain easy for me to edit or add new content later (e.g., new projects)
Deliverables
Fully built WordPress website
Clean, professional, modern design inspired by the reference sites
Mobile-responsive across all devices
SEO-ready structure and optimisations
Transfer of website and admin rights
Any design assets, templates, or documentation used

```html
<!DOCTYPE html>
<html lang="en">
<head>
<meta charset="utf-8">
<title>Valtorix Mechanical Design</title>
<link href="https://fonts.googleapis.com/css2?family=Poppins:wght@300;400;500;600&display=swap" rel="stylesheet">
<style>
:root{
  --blue:#2a55e6;
  --blue-deep:#1c3fc2;
  --ink:#16181f;
  --muted:#5d6270;
  --soft:#eef1f8;
  --line:#d9dde8;
  --white:#ffffff;
  --dark:#121317;
}
*{box-sizing:border-box;margin:0;padding:0}
html,body{width:1200px;height:5216px;overflow:hidden}
body{position:relative;background:var(--white);font-family:'Poppins',sans-serif;color:var(--ink)}
.section{position:absolute;left:0;width:1200px}
.btn{display:inline-block;background:var(--blue);color:var(--white);font-size:13px;font-weight:500;border-radius:20px;padding:10px 24px;text-decoration:none}
.section-title{text-align:center;font-size:40px;font-weight:400;color:var(--ink)}
.section-sub{text-align:center;font-size:14px;color:var(--muted);margin-top:6px}

/* header + hero */
.hero{top:0;height:640px;background:linear-gradient(180deg,#f4f5f8,#ffffff)}
.hero-photo{position:absolute;left:0;top:0;width:1200px;height:610px;border-radius:0 0 40px 40px;
  background:
    radial-gradient(ellipse 420px 260px at 720px 170px,rgba(120,132,158,.55),rgba(120,132,158,0) 70%),
    radial-gradient(ellipse 300px 200px at 960px 120px,rgba(70,82,110,.45),rgba(70,82,110,0) 70%),
    radial-gradient(ellipse 380px 220px at 250px 230px,rgba(170,180,200,.45),rgba(170,180,200,0) 70%),
    radial-gradient(ellipse 500px 240px at 900px 420px,rgba(200,208,224,.55),rgba(200,208,224,0) 70%),
    linear-gradient(180deg,#e9ecf2 0%,#f3f4f7 55%,#ffffff 100%)}
.hero-fade{position:absolute;left:0;top:300px;width:820px;height:310px;background:linear-gradient(90deg,rgba(255,255,255,.88),rgba(255,255,255,.55) 70%,rgba(255,255,255,0))}
.site-nav{position:absolute;top:40px;left:48px;right:40px;height:44px;display:flex;align-items:center}
.brand{display:flex;align-items:center;gap:10px;font-size:32px;font-weight:500;color:var(--blue-deep);width:250px}
.brand-dot{width:34px;height:34px;border-radius:50%;background:var(--blue)}
.nav-links{display:flex;gap:26px;list-style:none;font-size:12px;font-weight:500;letter-spacing:.5px;color:var(--ink);margin-left:44px}
.site-nav .btn{margin-left:auto;padding:9px 22px;font-size:12px}
.hero-title{position:absolute;left:48px;top:360px;font-size:78px;font-weight:300;line-height:1;letter-spacing:1px}
.hero-title span{display:block;color:var(--blue);font-size:58px;font-weight:400;margin-top:10px}
.hero-tag{position:absolute;left:50px;top:512px;font-size:24px;font-weight:300;letter-spacing:3px;color:var(--blue-deep)}
.hero-intro{position:absolute;left:850px;top:450px;width:300px;font-size:13px;line-height:1.55;color:var(--ink)}
.hero-scroll{position:absolute;left:1172px;top:150px;transform:rotate(90deg);transform-origin:left top;font-size:11px;letter-spacing:2px;color:var(--muted);white-space:nowrap}

/* expertise */
.expertise{top:640px;height:620px}
.expertise .section-title{margin-top:72px}
.expertise-grid{position:absolute;top:140px;left:60px;display:flex;gap:45px}
.expertise-card{width:330px;text-align:center}
.expertise-icon{width:60px;height:60px;border-radius:50%;background:var(--blue);margin:0 auto;display:flex;align-items:center;justify-content:center}
.expertise-card h3{font-size:20px;font-weight:500;margin-top:18px}
.expertise-card p{font-size:13px;color:var(--muted);line-height:1.5;margin:8px auto 0;width:240px}
.expertise-photo{height:230px;margin-top:22px;border-radius:6px}
.photo-office{background:radial-gradient(ellipse 140px 110px at 70% 35%,rgba(255,255,255,.55),rgba(255,255,255,0) 70%),radial-gradient(ellipse 120px 120px at 25% 75%,rgba(40,70,140,.7),rgba(40,70,140,0) 70%),linear-gradient(135deg,#c9d6ee 0%,#6f8fc6 50%,#2c3f6e 100%)}
.photo-cad{background:radial-gradient(ellipse 110px 70px at 40% 45%,rgba(150,200,255,.75),rgba(150,200,255,0) 70%),radial-gradient(ellipse 90px 60px at 78% 40%,rgba(120,170,240,.6),rgba(120,170,240,0) 70%),linear-gradient(160deg,#3c5a90 0%,#1e2e55 55%,#0f1730 100%)}
.photo-drafting{background:radial-gradient(ellipse 130px 90px at 30% 60%,rgba(120,126,140,.45),rgba(120,126,140,0) 70%),radial-gradient(ellipse 120px 80px at 75% 30%,rgba(190,170,140,.4),rgba(190,170,140,0) 70%),linear-gradient(135deg,#f4f4f2 0%,#dcdde0 50%,#b8bcc6 100%)}

/* services */
.services{top:1300px;height:640px;background:var(--soft);border-radius:24px;left:10px;width:1180px}
.services-head{position:absolute;left:38px;top:76px;font-size:40px;font-weight:400;line-height:1.15}
.services-copy{position:absolute;left:760px;top:84px;width:360px;font-size:13px;line-height:1.55;color:var(--ink)}
.services-copy .btn{margin-top:18px;font-size:11px;padding:8px 20px}
.service-rail{position:absolute;left:38px;top:250px;display:flex;gap:8px;height:350px}
.service-panel{position:relative;width:112px;height:350px;border-radius:8px;overflow:hidden}
.service-panel::after{content:"";position:absolute;inset:0;background:linear-gradient(180deg,rgba(40,70,180,.15),rgba(20,36,110,.75))}
.service-panel .label{position:absolute;z-index:1;left:34px;bottom:24px;transform:rotate(-90deg);transform-origin:left bottom;white-space:nowrap;color:var(--white);font-size:20px;font-weight:400}
.sp1{background:linear-gradient(170deg,#b8c3d8,#5e6f96 55%,#2a3560)}
.sp2{background:linear-gradient(170deg,#9aa4ba,#4c5a80 55%,#222c52)}
.sp3{background:linear-gradient(170deg,#c8ccd6,#78849f 55%,#2d375e)}
.sp4{background:linear-gradient(170deg,#a7b3cc,#566894 55%,#242e58)}
.sp6{background:linear-gradient(170deg,#8c96a8,#4a5676 55%,#1f2748)}
.sp7{background:linear-gradient(170deg,#d0d4dc,#8790a6 55%,#2f3860)}
.sp8{background:linear-gradient(170deg,#b0b6c4,#5c6684 55%,#252d52)}
.service-panel.open{width:264px;background:radial-gradient(ellipse 120px 80px at 55% 28%,rgba(160,205,255,.8),rgba(160,205,255,0) 70%),linear-gradient(170deg,#6f8fcc,#2e4a96 50%,#16204d)}
.service-panel.open h4{position:absolute;z-index:1;left:18px;top:170px;color:var(--white);font-size:22px;font-weight:400;line-height:1.2}
.service-panel.open p{position:absolute;z-index:1;left:18px;top:240px;width:228px;color:var(--white);font-size:11px;line-height:1.45}

/* case studies */
.cases{top:1960px;height:660px}
.cases .section-title{margin-top:64px}
.case-row{position:absolute;top:168px;left:80px;display:flex;gap:20px}
.case-card{width:340px}
.case-photo{height:224px;border-radius:4px}
.case-kart{background:radial-gradient(ellipse 110px 50px at 48% 55%,rgba(220,230,245,.55),rgba(220,230,245,0) 70%),radial-gradient(ellipse 200px 60px at 50% 80%,rgba(70,120,80,.5),rgba(70,120,80,0) 70%),linear-gradient(180deg,#0b0d12 0%,#1c2029 60%,#2a2f26 100%)}
.case-dct{background:radial-gradient(ellipse 110px 90px at 40% 50%,rgba(210,190,165,.8),rgba(210,190,165,0) 70%),radial-gradient(ellipse 80px 70px at 72% 45%,rgba(150,150,155,.7),rgba(150,150,155,0) 70%),linear-gradient(160deg,#c9bcad,#7a6a5c 55%,#3a3129)}
.case-switch{background:radial-gradient(ellipse 140px 80px at 50% 40%,rgba(210,216,226,.7),rgba(210,216,226,0) 70%),linear-gradient(90deg,#5a6478 0%,#9aa3b4 30%,#6d778c 55%,#a8b0bf 80%,#4b5468 100%)}
.case-card h3{font-size:20px;font-weight:400;margin-top:30px}
.case-card p{font-size:13px;color:var(--muted);line-height:1.5;margin-top:10px}
.case-card a{display:block;font-size:12px;color:var(--blue);margin-top:10px;text-decoration:none}
.slide-arrow{position:absolute;top:272px;width:30px;height:30px;border-radius:50%;background:var(--white);border:1px solid var(--line);display:flex;align-items:center;justify-content:center}
.cases .explore{position:absolute;left:540px;top:560px;font-size:11px;padding:8px 22px}

/* about */
.about{top:2672px;height:720px;left:14px;width:1172px;border-radius:28px;overflow:hidden;
  background:
    radial-gradient(ellipse 260px 200px at 80% 30%,rgba(240,220,200,.45),rgba(240,220,200,0) 70%),
    radial-gradient(ellipse 220px 160px at 58% 60%,rgba(90,170,220,.55),rgba(90,170,220,0) 70%),
    radial-gradient(ellipse 300px 200px at 20% 25%,rgba(150,170,230,.5),rgba(150,170,230,0) 70%),
    linear-gradient(135deg,#4a5fb8 0%,#2c3a8c 45%,#161c4a 100%)}
.about::after{content:"";position:absolute;left:0;top:300px;width:700px;height:420px;background:linear-gradient(90deg,rgba(24,32,90,.75),rgba(24,32,90,0))}
.about-title{position:absolute;z-index:1;left:36px;top:338px;font-size:46px;font-weight:300;color:var(--white);line-height:1.05}
.about-copy{position:absolute;z-index:1;left:36px;top:448px;width:560px;font-size:12px;line-height:1.55;color:#dfe4f7}
.about .btn{position:absolute;z-index:1;left:36px;top:574px;font-size:11px;padding:8px 20px}

/* testimonials */
.reviews{top:3392px;height:500px}
.reviews .section-title{margin-top:18px}
.review-track{position:absolute;top:112px;left:-150px;display:flex;gap:24px}
.review-card{width:264px;height:300px;background:var(--white);border:1px solid var(--line);border-radius:6px;padding:20px;position:relative;box-shadow:0 4px 14px rgba(20,30,70,.06)}
.reviewer{display:flex;align-items:center;gap:10px}
.avatar{width:36px;height:36px;border-radius:50%;background:var(--blue)}
.reviewer b{display:block;font-size:12px;font-weight:500}
.stars{color:#f5b400;font-size:11px;letter-spacing:1px}
.review-card p{font-size:12px;line-height:1.55;color:var(--ink);margin-top:16px}
.review-card small{position:absolute;left:20px;bottom:18px;font-size:10px;color:var(--muted)}
.review-badge{position:absolute;right:18px;bottom:16px;width:16px;height:16px;border-radius:50%;background:#c9ced9}
.quote-mark{position:absolute;right:20px;top:18px;font-size:40px;line-height:1;color:#c3c7d2}
.dots{position:absolute;top:446px;left:560px;display:flex;gap:8px}
.dots i{width:18px;height:4px;border-radius:2px;background:#c9cdd8}
.dots i.on{background:var(--ink)}

/* contact */
.contact{top:3920px;height:400px}
.contact h2{position:absolute;left:48px;top:100px;font-size:48px;font-weight:300}
.contact-line{position:absolute;left:48px;display:flex;gap:18px;align-items:flex-start}
.contact-icon{width:56px;height:56px;border-radius:50%;background:var(--blue);display:flex;align-items:center;justify-content:center;flex:none}
.contact-line div{font-size:30px;font-weight:300;line-height:1.3}
.contact-form{position:absolute;left:560px;top:40px;width:590px;height:320px;background:var(--blue);border-radius:6px;padding:28px 40px}
.field-row{display:flex;gap:24px;margin-bottom:14px}
.field{flex:1;height:36px;border:1px solid rgba(255,255,255,.55);border-radius:4px;color:var(--white);font-size:10px;padding:6px 10px}
.field.tall{height:92px}
.contact-form .send{display:inline-block;background:var(--white);color:var(--blue);font-size:11px;font-weight:500;border-radius:4px;padding:8px 18px;margin-top:4px}

/* CTA */
.cta{top:4440px;height:340px}
.cta-ring{position:absolute;left:90px;top:20px;width:230px;height:230px;border-radius:50%;border:40px solid #eef1fb}
.cta h2{text-align:center;font-size:44px;font-weight:400;line-height:1.15;margin-top:116px}
.cta p{text-align:center;font-size:14px;color:var(--muted);margin-top:8px}
.cta .btn{position:absolute;left:540px;top:282px;font-size:11px;padding:8px 24px}

/* footer */
.site-footer{top:4816px;height:370px;left:14px;width:1172px;border-radius:24px;background:var(--dark);color:var(--white)}
.newsletter{position:absolute;left:36px;top:96px;width:300px}
.newsletter .field{border-color:#6d7080;height:38px;display:flex;align-items:center}
.newsletter .sub{margin-top:10px;height:30px;background:var(--blue);border-radius:4px;text-align:center;font-size:11px;line-height:30px}
.footer-links{position:absolute;left:480px;top:80px;display:grid;grid-template-columns:150px 150px;row-gap:16px;list-style:none;font-size:14px;letter-spacing:.5px}
.footer-brand{position:absolute;right:36px;top:100px;display:flex;align-items:center;gap:16px;font-size:58px;font-weight:500}
.footer-brand .brand-dot{width:72px;height:72px}
.copyright{position:absolute;left:0;width:100%;top:326px;text-align:center;font-size:11px;letter-spacing:2px;color:#b9bcc7}
</style>
</head>
<body>

<header class="section hero">
  <div class="hero-photo" role="img" aria-label="Engineer's hand measuring a machined part with calipers over technical drawings"></div>
  <div class="hero-fade"></div>
  <nav class="site-nav">
    <div class="brand"><span class="brand-dot"></span>valtorix</div>
    <ul class="nav-links"><li>SERVICES</li><li>PROJECTS</li><li>PROCESS</li><li>SECTOR</li><li>CASE STUDIES</li><li>ABOUT</li><li>CONTACT</li></ul>
    <a class="btn" href="#">Request a Quote</a>
  </nav>
  <h1 class="hero-title">MECHANICAL<span>CAD Design</span></h1>
  <div class="hero-tag">Cutting Edge Engineering</div>
  <div class="hero-scroll">SCROLL TO EXPLORE</div>
  <p class="hero-intro">Welcome to Valtorix Mechanical Design. We are a UK based design consultancy offering a comprehensive mechanical and product design service from initial concepts through to full volume production.</p>
</header>

<section class="section expertise">
  <h2 class="section-title">Our Expertise</h2>
  <div class="expertise-grid">
    <div class="expertise-card">
      <div class="expertise-icon"><svg width="28" height="28" viewBox="0 0 24 24" fill="none" stroke="#fff" stroke-width="1.8"><path d="M4 20l6-6M14 4l6 6-8 8-6-6z"/></svg></div>
      <h3>Bespoke Product Design</h3>
      <p>Innovative design from concept through the full development life cycle</p>
      <div class="expertise-photo photo-office" role="img" aria-label="Engineers reviewing a product design at a workstation"></div>
    </div>
    <div class="expertise-card">
      <div class="expertise-icon"><svg width="28" height="28" viewBox="0 0 24 24" fill="none" stroke="#fff" stroke-width="1.8"><path d="M12 3l8 4.5v9L12 21l-8-4.5v-9z M12 12l8-4.5 M12 12v9 M12 12L4 7.5"/></svg></div>
      <h3>3D Modelling and Drawings</h3>
      <p>We create 3D CAD, 2D engineering drawings and photorealistic renders</p>
      <div class="expertise-photo photo-cad" role="img" aria-label="CAD model of a mechanical assembly on a monitor"></div>
    </div>
    <div class="expertise-card">
      <div class="expertise-icon"><svg width="28" height="28" viewBox="0 0 24 24" fill="none" stroke="#fff" stroke-width="1.8"><circle cx="12" cy="12" r="3.5"/><path d="M12 2v4M12 18v4M2 12h4M18 12h4M5 5l3 3M16 16l3 3M5 19l3-3M16 8l3-3"/></svg></div>
      <h3>Design for Manufacture</h3>
      <p>Creating designs optimised for prototype and production manufacture</p>
      <div class="expertise-photo photo-drafting" role="img" aria-label="Technical drawings with drafting tools on a desk"></div>
    </div>
  </div>
</section>

<section class="section services">
  <h2 class="services-head">Mechanical<br>Engineering Services</h2>
  <div class="services-copy">
    <p>We offer a comprehensive design service. Reconstructing accurate digital models of existing parts for redesign, improvement, replacement, or legacy documentation.</p>
    <a class="btn" href="#">Explore More</a>
  </div>
  <div class="service-rail">
    <div class="service-panel sp1" role="img" aria-label="Mechanical design workstation"><span class="label">Mechanical Design</span></div>
    <div class="service-panel sp2" role="img" aria-label="Design consultancy meeting"><span class="label">Design Consultancy</span></div>
    <div class="service-panel sp3" role="img" aria-label="3D model render"><span class="label">3D Modelling</span></div>
    <div class="service-panel sp4" role="img" aria-label="Project planning session"><span class="label">Project Management</span></div>
    <div class="service-panel open" role="img" aria-label="Engineer working on a manufacturing design on screen">
      <h4>Design for<br>Manufacture (DFM)</h4>
      <p>We bring a practical and manufacturing-aware approach to every part, shaping designs that build efficiently at scale.</p>
    </div>
    <div class="service-panel sp6" role="img" aria-label="Reverse engineering a component"><span class="label">Reverse Engineering</span></div>
    <div class="service-panel sp7" role="img" aria-label="3D printed prototype parts"><span class="label">3D Printing</span></div>
    <div class="service-panel sp8" role="img" aria-label="Prototype testing on a bench"><span class="label">Prototyping</span></div>
  </div>
</section>

<section class="section cases">
  <h2 class="section-title">Case Studies</h2>
  <p class="section-sub">Our previous projects matches the structure of top engineering agencies.</p>
  <div class="slide-arrow" style="left:36px"><svg width="12" height="12" viewBox="0 0 12 12"><path d="M8 2L4 6l4 4" stroke="#16181f" fill="none" stroke-width="1.6"/></svg></div>
  <div class="slide-arrow" style="left:1134px"><svg width="12" height="12" viewBox="0 0 12 12"><path d="M4 2l4 4-4 4" stroke="#16181f" fill="none" stroke-width="1.6"/></svg></div>
  <div class="case-row">
    <article class="case-card">
      <div class="case-photo case-kart" role="img" aria-label="Go-kart simulator rig in a dark studio"></div>
      <h3>Go-Kart Simulator Design</h3>
      <p>Our client already had an existing product, but wanted it updating and refreshing to offer their customers a better product.</p>
      <a href="#">Read more</a>
    </article>
    <article class="case-card">
      <div class="case-photo case-dct" role="img" aria-label="Dual clutch transmission cutaway"></div>
      <h3>Dual Clutch Transmission...</h3>
      <p>Our client already had an existing product, but wanted it updating and refreshing to offer their customers a better product.</p>
      <a href="#">Read more</a>
    </article>
    <article class="case-card">
      <div class="case-photo case-switch" role="img" aria-label="Electrical switchgear cabinets"></div>
      <h3>Electrical Switchgear</h3>
      <p>Our client already had an existing product, but wanted it updating and refreshing to offer their customers a better product.</p>
      <a href="#">Read more</a>
    </article>
  </div>
  <a class="btn explore" href="#">Explore all Works</a>
</section>

<section class="section about" role="img" aria-label="Design team collaborating around screens in a bright studio">
  <h2 class="about-title">About on<br>Valtorix Mechanical</h2>
  <p class="about-copy">Owen Hartley is the Chief Engineer at Valtorix Mechanical Design. He has 15 years experience working as a mechanical design engineer across many industries, including high performance automotive, aerospace, defence and consumer products. He has worked on multiple roles across a wide range of products.</p>
  <a class="btn" href="#">Tell us about your Ideas</a>
</section>

<section class="section reviews">
  <h2 class="section-title">Our Customers Say’s</h2>
  <p class="section-sub">Feedback from some of our recent customers</p>
  <div class="review-track">
    <div class="review-card"><span class="quote-mark">“</span><p>I had the pleasure of working alongside the team on a day-to-day basis to deliver the most complex machined casting for an 8-speed DCT transmission for an OEM customer.</p><small>Reviewed on</small><span class="review-badge"></span></div>
    <div class="review-card"><div class="reviewer"><span class="avatar"></span><div><b>Daniel Reeve</b><span class="stars">★★★★★</span></div></div><span class="quote-mark">“</span><p>I had the pleasure of working alongside the team on a day-to-day basis to deliver the most complex machined casting for an 8-speed DCT transmission for an OEM customer. Read more</p><small>Reviewed on</small><span class="review-badge"></span></div>
    <div class="review-card"><div class="reviewer"><span class="avatar"></span><div><b>Daniel Reeve</b><span class="stars">★★★★★</span></div></div><span class="quote-mark">“</span><p>I had the pleasure of working alongside the team on a day-to-day basis to deliver the most complex machined casting for an 8-speed DCT transmission for an OEM customer. Read more</p><small>Reviewed on</small><span class="review-badge"></span></div>
    <div class="review-card"><div class="reviewer"><span class="avatar"></span><div><b>Daniel Reeve</b><span class="stars">★★★★★</span></div></div><span class="quote-mark">“</span><p>I had the pleasure of working alongside the team on a day-to-day basis to deliver the most complex machined casting for an 8-speed DCT transmission for an OEM customer. Read more</p><small>Reviewed on</small><span class="review-badge"></span></div>
    <div class="review-card"><div class="reviewer"><span class="avatar"></span><div><b>Daniel Reeve</b><span class="stars">★★★★★</span></div></div><span class="quote-mark">“</span><p>I had the pleasure of working alongside the team on a day-to-day basis to deliver the most complex machined casting for an 8-speed DCT transmission.</p><small>Reviewed on</small><span class="review-badge"></span></div>
  </div>
  <div class="dots"><i></i><i class="on"></i><i></i><i></i></div>
</section>

<section class="section contact">
  <h2>Get In Touch</h2>
  <div class="contact-line" style="top:196px">
    <span class="contact-icon"><svg width="26" height="26" viewBox="0 0 24 24" fill="#fff"><path d="M6.6 10.8a15 15 0 006.6 6.6l2.2-2.2a1 1 0 011-.25 11.4 11.4 0 003.6.57 1 1 0 011 1V20a1 1 0 01-1 1A17 17 0 013 4a1 1 0 011-1h3.5a1 1 0 011 1c0 1.25.2 2.45.57 3.57a1 1 0 01-.25 1z"/></svg></span>
    <div>CALL NOW :<br>+44 (0) 7700 900418</div>
  </div>
  <div class="contact-line" style="top:300px">
    <span class="contact-icon"><svg width="26" height="26" viewBox="0 0 24 24" fill="none" stroke="#fff" stroke-width="1.8"><rect x="3" y="5" width="18" height="14" rx="2"/><path d="M3 7l9 6 9-6"/></svg></span>
    <div>EMAIL NOW :<br>info@valtorix.design</div>
  </div>
  <form class="contact-form">
    <div class="field-row"><div class="field">First Name*</div><div class="field">Last Name*</div></div>
    <div class="field-row"><div class="field">E-mail*</div><div class="field">Phone</div></div>
    <div class="field-row"><div class="field">Choose Service</div></div>
    <div class="field-row"><div class="field tall">Message</div></div>
    <span class="send">Send Now</span>
  </form>
</section>

<section class="section cta">
  <div class="cta-ring"></div>
  <h2>Let’s Build Your<br>Next Mechanical Solution</h2>
  <p>Share your project requirements — I’ll respond within one business day.</p>
  <a class="btn" href="#">Start a Project</a>
</section>

<footer class="section site-footer">
  <div class="newsletter">
    <div class="field">Enter Your Email</div>
    <div class="sub">Subscribe</div>
  </div>
  <ul class="footer-links"><li>SERVICES</li><li>CASE STUDIES</li><li>PROJECTS</li><li>ABOUT</li><li>PROCESS</li><li>CONTACT</li><li>SECTOR</li></ul>
  <div class="footer-brand"><span class="brand-dot"></span>valtorix</div>
  <div class="copyright">© VALTORIX MECHANICAL DESIGN 2025</div>
</footer>

</body>
</html>
```